Venture Capital Investment Firm

We are looking to overhaul our existing website (substantially), with only using the same logos (which we can provide).
We are an investment firm that focuses on making loans to late stage technology companies. Our site should ultimately look like other venture capital firms, and look modern and fresh. We have an existing website www.norvellhub.com which this will be replacing, although we will be using a lot of the existing written content, and potentially the numbers of pages we will need, we are not wed to anything else. Please feel free to shoot any questions at any time and thank you in advance for your help!
Websites we like as examples:
https://www.tesmarkfund.com/
https://www.brindlewoodpartners.com/
Target Market(s)
Potential investors who will invest in our firm, as well as potentially companies that are looking to borrow money from us.
Coding
Coded - Design and coding required
Number of Pages Required
5+ page
Colors
Designer to choose colors to be used in the design.
Look and feel

```html
<!DOCTYPE html>
<html lang="en">
<head>
<meta charset="utf-8">
<title>Norvell Hub Investment Partners</title>
<link rel="stylesheet" href="https://fonts.googleapis.com/css2?family=Cinzel:wght@600;700&family=Oswald:wght@400;500&family=Montserrat:wght@400;500&display=swap">
<style>
:root{
  --navy:#0a0a6b;
  --hero:#1c2290;
  --hero-deep:#121a7a;
  --sky:#8fb4f0;
  --ink:#0a0a5e;
  --text:#555;
  --muted:#8a8a8a;
  --panel:#f4f4f6;
  --line:#dcdce2;
  --white:#fff;
}
*{margin:0;padding:0;box-sizing:border-box}
html,body{width:1200px;height:3477px;overflow:hidden}
body{position:relative;font-family:'Montserrat',sans-serif;color:var(--text);background:var(--white)}
.abs{position:absolute}
.serif{font-family:'Cinzel',serif}

/* hero */
.hero{position:absolute;left:0;top:0;width:1200px;height:677px;background:linear-gradient(120deg,var(--hero-deep),var(--hero) 60%,#2530a0)}
.hero-art{position:absolute;left:640px;top:150px;width:460px;height:527px;border-radius:230px 230px 0 0;background:linear-gradient(160deg,#5a82d8,var(--sky) 60%,#c8dcf8);opacity:.85}
.brand{position:absolute;left:78px;top:18px;display:flex;align-items:center;gap:12px;color:var(--white)}
.brand-mark{width:14px;height:14px;background:var(--white)}
.brand-name{font-family:'Cinzel',serif;font-weight:600;font-size:26px;letter-spacing:.5px;line-height:1}
.brand-sub{font-family:'Cinzel',serif;font-weight:600;font-size:8px;letter-spacing:.5px;margin-top:3px}
.nav{position:absolute;right:80px;top:32px;display:flex;gap:26px;font-size:14px;color:var(--white);letter-spacing:.3px}
.hero-title{position:absolute;left:78px;top:236px;font-family:'Oswald',sans-serif;font-weight:500;font-size:40px;line-height:47px;color:var(--white);letter-spacing:.3px}
.hero-sub{position:absolute;left:78px;top:386px;font-family:'Oswald',sans-serif;font-size:18px;color:var(--white)}
.btn{display:flex;align-items:center;justify-content:center;background:var(--white);color:var(--ink);border-radius:30px;font-family:'Cinzel',serif;font-weight:700}
.hero .btn{position:absolute;left:77px;top:440px;width:187px;height:52px;font-size:18px}

/* about */
.about-brand{position:absolute;left:78px;top:790px;display:flex;align-items:center;gap:18px}
.about-brand .mark{width:26px;height:26px;background:var(--ink)}
.about-brand .name{font-family:'Cinzel',serif;font-weight:600;font-size:108px;color:var(--ink);line-height:1}
.about-lede{position:absolute;left:78px;top:973px;width:580px;font-size:23px;line-height:33px;color:#222}
.eyebrow{position:absolute;left:78px;top:1114px;font-size:15px;font-weight:500;color:var(--ink)}
.stat{position:absolute;top:1148px;text-align:center}
.stat b{display:block;font-family:'Cinzel',serif;font-weight:600;font-size:40px;color:var(--ink);line-height:48px}
.stat span{display:block;font-size:14px;line-height:27px;color:var(--muted);margin-top:4px}
.tiles{position:absolute;left:769px;top:752px;width:354px;height:573px;display:grid;grid-template-columns:1fr 1fr;grid-template-rows:188px 188px 197px;border:1px solid var(--line);background:var(--panel)}
.tile{border-right:1px solid var(--line);border-bottom:1px solid var(--line);display:flex;flex-direction:column;align-items:center;justify-content:center;text-align:center;font-size:15px;line-height:29px;color:var(--ink);gap:12px}
.tile:nth-child(2n){border-right:0}
.tile:nth-child(n+5){border-bottom:0}
.tile svg{width:46px;height:46px;fill:none;stroke:var(--ink);stroke-width:1.6}

/* testimonials */
.quotes{position:absolute;left:0;top:1413px;width:1200px;height:475px;background:var(--panel)}
.section-title{position:absolute;left:0;width:1200px;text-align:center;font-family:'Cinzel',serif;font-weight:700;font-size:40px;color:var(--ink)}
.avatar{position:absolute;left:75px;top:172px;width:160px;height:160px;border-radius:50%;border:3px solid var(--ink);background:linear-gradient(135deg,#c9a58e,#8a5a4a)}
.quote{position:absolute;left:280px;top:177px;width:826px;font-size:15px;line-height:27px;color:#777}
.signer{position:absolute;left:280px;top:277px;font-family:'Cinzel',serif;font-weight:700;font-size:20px;color:var(--ink)}
.dots{position:absolute;left:529px;top:380px;display:flex;gap:16px}
.dots i{width:16px;height:16px;border-radius:50%;border:2px solid var(--ink)}
.dots i:first-child{background:var(--ink)}

/* team */
.team{position:absolute;left:0;top:1888px;width:1200px;height:610px;background:var(--navy)}
.team .section-title{color:var(--white);top:55px}
.member{position:absolute;top:126px;width:323px;height:313px;background:linear-gradient(#f2f2f2,#cfcfcf)}
.member .cap{position:absolute;left:0;bottom:0;width:100%;height:83px;background:rgba(28,34,144,.85);text-align:center;color:var(--white)}
.member .cap b{display:block;font-family:'Cinzel',serif;font-weight:700;font-size:22px;margin-top:14px}
.member .cap span{font-size:15px}
.team .btn{position:absolute;left:436px;top:469px;width:328px;height:52px;font-size:18px}

/* news */
.news .section-title{top:2583px}
.card{position:absolute;top:2678px;width:323px;height:275px;background:var(--panel);padding:22px 20px}
.card h3{font-size:16px;font-weight:500;line-height:23px;color:var(--ink)}
.card time{display:block;font-family:'Cinzel',serif;font-size:15px;color:#999;margin:10px 0 20px}
.card p{font-size:14px;line-height:27px;color:#888}
.card a{display:inline-block;margin-top:14px;font-family:'Cinzel',serif;font-weight:700;font-size:17px;color:var(--ink);text-decoration:underline}

/* footer */
.footer{position:absolute;left:0;top:3070px;width:1200px;height:346px;background:var(--navy);color:var(--white)}
.footer .brand{left:98px;top:122px}
.disclaimer{position:absolute;left:174px;top:196px;font-size:15px;color:var(--white);text-decoration:underline}
.col-title{position:absolute;top:42px;font-family:'Cinzel',serif;font-weight:700;font-size:19px}
.contact-row{position:absolute;left:433px;display:flex;gap:26px;font-size:14px;line-height:27px;color:#d6d8f2}
.contact-row svg{width:22px;height:22px;fill:var(--white);margin-top:2px;flex:none}
.newsletter{position:absolute;left:793px;top:78px;width:320px;font-size:14px;line-height:27px;color:#d6d8f2}
.field{position:absolute;left:790px;width:323px;height:46px;border:1px solid #2e3390;background:#151a80;font-size:14px;color:#d6d8f2;padding:14px 15px}
.footer .btn{position:absolute;left:790px;top:253px;width:162px;height:51px;font-size:18px}
.legal{position:absolute;left:0;top:3416px;width:1200px;height:61px;background:#f1f1f1;text-align:center;line-height:61px;font-size:14px;color:var(--ink)}
</style>
</head>
<body>

<header class="hero">
  <div class="hero-art" role="img" aria-label="Upward view of a glass office tower in blue light"></div>
  <div class="brand">
    <div class="brand-mark"></div>
    <div><div class="brand-name">Norvell Hub</div><div class="brand-sub">INVESTMENT PARTNERS, LLC</div></div>
  </div>
  <nav class="nav"><span>HOME</span><span>STRATEGY</span><span>ABOUT US</span><span>TEAM</span><span>NEWS</span><span>CONTACT</span><span>INVESTORS</span></nav>
  <h1 class="hero-title">WE ARE A GLOBAL STRUCTURED<br>CREDIT INVESTMENT FIRM<br>FOCUSED ON THE</h1>
  <p class="hero-sub">HEALTHCARE AND TECHNOLOGY INDUSTRIES</p>
  <span class="btn">LEARN MORE</span>
</header>

<section class="about">
  <div class="about-brand"><div class="mark"></div><div class="name">Norvell</div></div>
  <p class="about-lede">We take a different approach to providing growth capital with structured credit solutions for proven innovators in technology</p>
  <p class="eyebrow">OUR EXPERIENCE</p>
  <div class="stat" style="left:88px;width:150px"><b>$1.2B</b><span>Over $1.2B invested<br>by our partners</span></div>
  <div class="stat" style="left:258px;width:185px"><b>40+</b><span>40 Life science and<br>technology investments</span></div>
  <div class="stat" style="left:470px;width:200px"><b>12+</b><span>Over a decade innovating<br>financing structures</span></div>

  <div class="tiles">
    <div class="tile"><svg viewBox="0 0 46 46"><path d="M23 4a12 12 0 0 0-7 22v6h14v-6A12 12 0 0 0 23 4z"/><path d="M17 36h12M18 40h10"/></svg><span>WE STARTED<br>WITH A BIG IDEA</span></div>
    <div class="tile"><svg viewBox="0 0 46 46"><circle cx="18" cy="26" r="9"/><circle cx="18" cy="26" r="3"/><circle cx="34" cy="14" r="6"/><circle cx="34" cy="30" r="5"/></svg><span>WHAT WE LOOK<br>FOR</span></div>
    <div class="tile"><svg viewBox="0 0 46 46"><circle cx="23" cy="15" r="6"/><circle cx="11" cy="19" r="5"/><circle cx="35" cy="19" r="5"/><path d="M12 36c0-7 5-12 11-12s11 5 11 12M2 34c0-5 4-8 9-8M44 34c0-5-4-8-9-8"/></svg><span>OUR TEAM</span></div>
    <div class="tile"><svg viewBox="0 0 46 46"><circle cx="23" cy="17" r="13"/><path d="M17 17l4 4 8-8M15 28l-4 14 6-3 4 5 2-9M31 28l4 14-6-3-4 5"/></svg><span>OUR VALUES</span></div>
    <div class="tile"><svg viewBox="0 0 46 46"><circle cx="25" cy="13" r="9"/><path d="M25 8v10M22 11h5M4 32l8-5h10l6 3h8l-6 5H20M4 40l10-2 16 0 12-10"/></svg><span>OUR INVESTMENTS</span></div>
    <div class="tile"><svg viewBox="0 0 46 46"><rect x="6" y="8" width="34" height="30"/><path d="M2 12v26h4M12 14h22M12 20h22M12 26h22M12 32h22"/></svg><span>NEWS</span></div>
  </div>
</section>

<section class="quotes">
  <h2 class="section-title" style="top:70px">WHAT OUR PARTNERS SAY</h2>
  <div class="avatar" role="img" aria-label="Portrait photo of a partner"></div>
  <p class="quote">Lorem Ipsum is simply dummy text of the printing and typesetting industry. Lorem Ipsum has been the industry's standard dummy text ever since the 1500s, when an unknown printer took a galley of type and scrambled it to make a type specimen book.</p>
  <p class="signer">CEO - PARTNER NAME</p>
  <div class="dots"><i></i><i></i><i></i><i></i><i></i></div>
</section>

<section class="team">
  <h2 class="section-title">MEET OUR TEAM</h2>
  <div class="member" style="left:77px" role="img" aria-label="Black and white portrait of Elias Marrow"><div class="cap"><b>ELIAS MARROW</b><span>Managing Partner</span></div></div>
  <div class="member" style="left:439px" role="img" aria-label="Black and white portrait of Samir Qadir"><div class="cap"><b>SAMIR QADIR</b><span>Managing Partner</span></div></div>
  <div class="member" style="left:800px" role="img" aria-label="Black and white portrait of Owen Pratt"><div class="cap"><b>OWEN PRATT</b><span>Partner</span></div></div>
  <span class="btn">KNOW MORE ABOUT TEAM</span>
</section>

<section class="news">
  <h2 class="section-title">NORVELL NEWS</h2>
  <article class="card" style="left:77px"><h3>Norvell Hub completes structured debt investment in Brightpath</h3><time>APRIL 30, 2018</time><p>Norvell Hub Investment Partners ("Norvell Hub") announced today that it has completed a structured...</p><a>READ MORE</a></article>
  <article class="card" style="left:439px;height:300px"><h3>Norvell Hub completes $22,000,000 structured debt investment in Questora</h3><time>OCTOBER 19, 2016</time><p>Norvell Hub Investment Partners ("Norvell Hub") announced today that it has completed a $22,000,000...</p><a>READ MORE</a></article>
  <article class="card" style="left:800px"><h3>Halvern Semiconductor acquired by Voltrix for $55,000,000</h3><time>APRIL 4, 2016</time><p>Voltrix, Inc., a leading supplier of advanced semiconductor communications components for...</p><a>READ MORE</a></article>
</section>

<footer class="footer">
  <div class="brand">
    <div class="brand-mark"></div>
    <div><div class="brand-name">Norvell Hub</div><div class="brand-sub">INVESTMENT PARTNERS, LLC</div></div>
  </div>
  <span class="disclaimer">Legal Disclaimer</span>

  <h4 class="col-title" style="left:435px">CONTACT US</h4>
  <div class="contact-row" style="top:84px"><svg viewBox="0 0 24 24"><path d="M12 1a8 8 0 0 0-8 8c0 6 8 14 8 14s8-8 8-14a8 8 0 0 0-8-8zm0 11a3 3 0 1 1 0-6 3 3 0 0 1 0 6z"/></svg><div>SAN FRANCISCO<br>2250 Harlow Street #318<br>San Francisco, CA 94103</div></div>
  <div class="contact-row" style="top:183px"><svg viewBox="0 0 24 24"><path d="M2 5h20v3l-10 6L2 8zM2 10l10 6 10-6v9H2z"/></svg><div>GENERAL INQUIRIES : :<br>inquiries@norvellhub.com</div></div>
  <div class="contact-row" style="top:253px"><svg viewBox="0 0 24 24"><path d="M2 5h20v3l-10 6L2 8zM2 10l10 6 10-6v9H2z"/></svg><div>MEDIA INQUIRIES :<br>media@norvellhub.com</div></div>

  <h4 class="col-title" style="left:793px">NEWSLETTER</h4>
  <p class="newsletter">Would you like to receive our exclusive news and update for signup our newsletter !</p>
  <div class="field" style="top:140px">Enter Name *</div>
  <div class="field" style="top:195px">Enter Email *</div>
  <span class="btn">SUBSCRIBE</span>
</footer>
<div class="legal">©2019 Norvell Hub Investment Partners LLC.&nbsp; All Rights Reserved.</div>

</body>
</html>
```